Cocktail-Making Assistant App re-design

Ok boys and girls, here's the deal:
I have an android app which is almost complete, but needs a design overhaul.

The app is a standard cocktail-making assistant: gives you a list of cocktails and the ability to see which cocktail you can make out of those ingredients (drinks, fruit, etc) you have at home.

I've attached some general app flow, as well as detailed requirements/explanation presentation. Most of those things are just FYI, so that you know what it's about.

3 screens are the most important (main screen, cocktail view screen, ingredient view screen), meaning I will pick the design mostly based on ideas for those 3 things, with the fourth being a rather simple list (given on attached flow, third tier)
Some other screens are derived from that, with some minor changes on it, but you shouldn't care about that.

There are lots of other, non-explained things which I said nothing about only because they are (from design point of view) completely the same and would only make it seem more complicated.

I don't want to influence the colour scheme, but the app will be released under RedFig developer name (having a light colured red fig as a logo) so I suppose some brownish design, for example, will not really fit nicely. If you, however, have a killer which you are confident will prove me wrong, I'm looking forward to seeing it!

It should be a serious, elegant look (as opposed to cartoonish, but we are not aiming for a business look at all!), not cluttered with details, no clubbing themes, glitter and so on.

Test apk file available on request (Android 2.3+).

Edit: payment is now guaranteed
Also please note that currently, the favorite, "heart" button has a motion effect:
on click it flies out of the screen to the left (white heart) and comes back to the screen as a red heart. Take that into consideration, if it means anything to you.

Target Market(s)

Whoever you imagine would enjoy drinking cocktails

Industry/Entity Type

Business

Requirements
Must have
• Everything is said in the provided documentation - images say more than I could possibly write here.
Nice to have
• As said, most of the icons are a nice-to-have. Only those which are critically linked to the rest of the design must be provided. More details in the docs.
Should not have
• No cartoon look, No zillion colours

```html
<!DOCTYPE html>
<html lang="en">
<head>
<meta charset="utf-8">
<title>151 Florida Bushwacker</title>
<link rel="stylesheet" href="https://fonts.googleapis.com/css2?family=Michroma&display=swap">
<style>
:root{
  --ink:#1e1e1e;
  --accent:#d8232a;
  --panel:#f6f6f6;
  --green:#acd377;
  --orange:#fbb55f;
  --red:#fc5d63;
  --taupe:#ccaea4;
  --yellow:#fee674;
  --lilac:#b1a9e9;
  --divider:#d6d6d6;
}
*{box-sizing:border-box;margin:0;padding:0}
html,body{width:676px;height:1200px;overflow:hidden;background:#fff}
.screen{width:640px;height:1136px;transform:scale(1.05625);transform-origin:0 0;position:relative;font-family:"Michroma",sans-serif;color:var(--ink);text-transform:uppercase}
.topbar{height:92px;display:flex;align-items:stretch;background:linear-gradient(#fbfbfb,#ececec)}
.topbar .nav{width:124px;display:flex;align-items:center;padding-left:8px;border-right:1px solid var(--divider)}
.topbar .title{flex:1;padding:22px 0 0 18px;font-size:20px;line-height:29px;letter-spacing:1px}
.topbar .camera{width:124px;border-left:1px solid var(--divider);display:flex;align-items:center;justify-content:center}
.accent-band{height:8px;background:linear-gradient(var(--accent),#a8141a)}
.summary{height:160px;background:var(--panel);position:relative}
.summary .drink-photo{position:absolute;left:62px;top:22px;width:142px;height:112px;border-radius:10px;background:linear-gradient(135deg,#f6a32a,#c3d66b 45%,#6b2a16)}
.summary .rating{position:absolute;left:242px;top:30px;width:236px;display:flex;gap:8px;padding-left:12px;padding-bottom:6px;border-bottom:1px solid var(--divider)}
.summary .vol{position:absolute;left:242px;top:86px;font-size:15px;letter-spacing:1px}
.summary .favourite{position:absolute;left:528px;top:44px}
.ingredient{height:130px;position:relative;display:flex;align-items:center}
.ingredient .mark{position:absolute;left:107px;top:50%;transform:translateY(-50%)}
.ingredient .name{position:absolute;left:240px;top:50%;transform:translateY(-50%);font-size:16px;letter-spacing:1px;line-height:29px}
.ingredient .name small{display:block;font-size:11px;color:#fff;line-height:12px;margin-top:-4px}
.ingredient .cart{position:absolute;left:528px;top:50%;transform:translateY(-50%)}
.green{background:var(--green)}.orange{background:var(--orange)}.red{background:var(--red)}
.taupe{background:var(--taupe)}.yellow{background:var(--yellow)}.lilac{background:var(--lilac)}
.hint{position:absolute;left:0;bottom:0;width:640px;height:92px;background:linear-gradient(#f4f4f4,#dcdcdc);text-align:center;padding-top:24px;font-size:11px;letter-spacing:1px;color:#666;box-shadow:0 -2px 6px rgba(0,0,0,.12)}
.hint svg{display:block;margin:12px auto 0}
</style>
</head>
<body>
<svg width="0" height="0" style="position:absolute">
  <defs>
    <symbol id="star" viewBox="0 0 24 24"><path d="M12 1l3.2 7.2 7.8.7-5.9 5.2 1.8 7.7L12 17.8 5.1 21.8l1.8-7.7L1 8.9l7.8-.7z"/></symbol>
    <symbol id="cart" viewBox="0 0 92 80">
      <path d="M4 14h14l10 38h48l10-30H30" fill="none" stroke="#222" stroke-width="7" stroke-linejoin="round" stroke-linecap="round"/>
      <rect x="48" y="14" width="13" height="32" rx="3" transform="rotate(28 54 30)" fill="#222"/>
      <rect x="60" y="2" width="5" height="12" transform="rotate(28 62 8)" fill="#222"/>
      <circle cx="36" cy="70" r="7" fill="#222"/><circle cx="70" cy="70" r="7" fill="#222"/>
    </symbol>
  </defs>
</svg>
<main class="screen">
  <header class="topbar">
    <div class="nav">
      <svg width="80" height="54" viewBox="0 0 80 54"><path d="M14 18l-10 9 10 9" fill="none" stroke="var(--accent)" stroke-width="3"/><path d="M46 4L22 26h7v22h12V34h10v14h12V26h7L60 16V6h-6v5z" fill="#111"/></svg>
    </div>
    <div class="title">151 Florida<br>Bushwacker</div>
    <div class="camera">
      <svg width="62" height="46" viewBox="0 0 62 46"><path d="M4 10h14l5-8h16l5 8h14v34H4z" fill="#111"/><circle cx="31" cy="27" r="12" fill="#fff"/><circle cx="31" cy="27" r="7" fill="#111"/></svg>
    </div>
  </header>
  <div class="accent-band"></div>
  <section class="summary">
    <div class="drink-photo" role="img" aria-label="Assorted cocktails in glasses"></div>
    <div class="rating">
      <svg width="32" height="32" fill="#acd377"><use href="#star"/></svg>
      <svg width="32" height="32" fill="#fbb55f"><use href="#star"/></svg>
      <svg width="32" height="32" fill="#f24b54"><use href="#star"/></svg>
      <svg width="32" height="32" fill="#b1a9e9"><use href="#star"/></svg>
      <svg width="32" height="32" fill="#ccaea4"><use href="#star"/></svg>
    </div>
    <div class="vol">Vol unavailable</div>
    <svg class="favourite" width="92" height="66" viewBox="0 0 92 66"><path d="M38 62C10 42 4 30 4 18 4 9 11 2 20 2c8 0 14 5 18 11C42 7 48 2 56 2c9 0 16 7 16 16 0 12-6 24-34 44z" fill="#333"/><circle cx="70" cy="44" r="20" fill="#333" stroke="#f6f6f6" stroke-width="4"/><path d="M70 33v22M59 44h22" stroke="#fff" stroke-width="4"/></svg>
  </section>

  <div class="ingredient green">
    <svg class="mark" width="30" height="30" fill="#222"><use href="#star"/></svg>
    <div class="name">1/2 oz Palmera rum</div>
    <svg class="cart" width="92" height="80"><use href="#cart"/><circle cx="14" cy="32" r="10" fill="#222"/><path d="M9 32l4 4 6-7" fill="none" stroke="var(--green)" stroke-width="2.5"/></svg>
  </div>
  <div class="ingredient orange">
    <svg class="mark" width="30" height="30" fill="#222"><use href="#star"/></svg>
    <div class="name">1/2 oz light rum</div>
    <svg class="cart" width="92" height="80"><use href="#cart"/><circle cx="14" cy="32" r="10" fill="#222"/><path d="M14 26v12M8 32h12" stroke="var(--orange)" stroke-width="2.5"/></svg>
  </div>
  <div class="ingredient red">
    <svg class="mark" width="30" height="30" fill="#222"><use href="#star"/></svg>
    <div class="name">1 oz 151 proof rum<small>Marlow</small></div>
    <svg class="cart" width="92" height="80"><use href="#cart"/><circle cx="14" cy="32" r="10" fill="#222"/><path d="M14 26v12M8 32h12" stroke="var(--red)" stroke-width="2.5"/></svg>
  </div>
  <div class="ingredient taupe">
    <svg class="mark" width="30" height="30" fill="#222"><use href="#star"/></svg>
    <div class="name">1 oz dark creme<br>&nbsp;&nbsp;&nbsp;&nbsp;de cacao</div>
    <svg class="cart" width="92" height="80"><use href="#cart"/><circle cx="14" cy="32" r="10" fill="#222"/><path d="M9 32l4 4 6-7" fill="none" stroke="var(--taupe)" stroke-width="2.5"/></svg>
  </div>
  <div class="ingredient yellow">
    <svg class="mark" width="30" height="30" fill="#222"><use href="#star"/></svg>
    <div class="name">1 oz Solenne</div>
    <svg class="cart" width="92" height="80"><use href="#cart"/></svg>
  </div>
  <div class="ingredient lilac">
    <svg class="mark" width="30" height="30" fill="#222"><use href="#star"/></svg>
    <div class="name">1 oz milk</div>
    <svg class="cart" width="92" height="80"><use href="#cart"/></svg>
  </div>

  <footer class="hint">
    Pull up to view details about making this cocktail.
    <svg width="20" height="20" viewBox="0 0 20 20"><path d="M10 18V4M4 10l6-6 6 6" fill="none" stroke="#666" stroke-width="3"/></svg>
  </footer>
</main>
</body>
</html>
```